Logo + Label Design (Men’s Grooming Brand & Product Packaging)

Design a logo and 2 oz pomade label for Brel, a modern men’s grooming brand focused on clean, high-quality, natural ingredients. The design should establish a bold, masculine, minimalist identity that can later extend to products like shaving gel and body wash.

Key Requirements

Create a primary logo for “Brel” and a core label for the 2 oz pomade jar (screw-top).

Use a clean, modern style — masculine, confident, and approachable (think Dorran’s, Velta, Northfield Kit).

Design for 1–2 color screen printing on solid jar colors (white, black, or navy).

Avoid gradients, foil, or embossing. Must work in black & white.

Provide: vector logo, mockup of the 2 oz jar, color palette (CMYK/RGB/HEX), and font specs.

Winning design may lead to future projects (body wash, shave gel, skincare lines).

Font styles to use
Other font styles liked:
• We like the fonts and design concept in the attached mockup.

Requirements
Should not have
• We want to avoid too much writing or busy designs. We want to avoid having graphics/illustrations embedded in the logo if they will cause the brand to look less classy or sophisticated. We also want the design to look simple and all-American (e.g. Hollister and Vane, Pine Ledger, The KIM, etc). We’d like to give a Pellham & Royce vibe that feels classy and high end.

```html
<!DOCTYPE html>
<html lang="en">
<head>
<meta charset="utf-8">
<title>Brel Hair Pomade Lid Label</title>
<link rel="stylesheet" href="https://fonts.googleapis.com/css2?family=Open+Sans:wght@400;600;700&display=swap">
<style>
  :root {
    --backdrop: #f3f3f3;
    --lid: #070908;
    --ink: #ffffff;
  }
  * { margin: 0; padding: 0; box-sizing: border-box; }
  html, body {
    width: 1200px;
    height: 1000px;
    overflow: hidden;
    background: var(--backdrop);
  }
  .canvas {
    position: relative;
    width: 1200px;
    height: 1000px;
    font-family: "Open Sans", Arial, sans-serif;
    color: var(--ink);
  }
  .lid {
    position: absolute;
    left: 276px;
    top: 174px;
    width: 649px;
    height: 649px;
    border-radius: 50%;
    background: var(--lid);
  }
  .wordmark {
    position: absolute;
    left: 0;
    width: 1200px;
    top: 330px;
    text-align: center;
    font-size: 200px;
    font-weight: 600;
    line-height: 240px;
    letter-spacing: 2px;
  }
  .registered {
    position: absolute;
    left: 781px;
    top: 358px;
    font-size: 24px;
    font-weight: 400;
    line-height: 28px;
  }
  .spec-table {
    position: absolute;
    left: 423px;
    top: 619px;
    width: 356px;
    height: 69px;
    border: 1px solid var(--ink);
    display: grid;
    grid-template-columns: 251px 1fr;
    grid-template-rows: 34px 1fr;
  }
  .spec-table > div {
    display: flex;
    align-items: center;
    justify-content: center;
  }
  .product-name {
    font-size: 24px;
    font-weight: 700;
    letter-spacing: 0.5px;
    border-right: 1px solid var(--ink);
    border-bottom: 1px solid var(--ink);
  }
  .net-weight {
    font-size: 16px;
    font-weight: 600;
    border-bottom: 1px solid var(--ink);
  }
  .net-weight .metric { font-size: 12px; margin-left: 8px; }
  .scent {
    font-size: 17px;
    font-weight: 600;
    letter-spacing: 0.5px;
    border-right: 1px solid var(--ink);
  }
  .finish-notes {
    flex-direction: column;
    font-size: 12px;
    line-height: 15px;
  }
  .finish-notes .hold {
    border-bottom: 1px solid var(--ink);
    padding: 0 1px 1px;
  }
</style>
</head>
<body>
  <main class="canvas">
    <div class="lid"></div>
    <div class="wordmark">brel</div>
    <div class="registered">®</div>
    <section class="spec-table">
      <div class="product-name">HAIR POMADE</div>
      <div class="net-weight">2oz<span class="metric">(57g)</span></div>
      <div class="scent">FRESH &amp; CLEAN</div>
      <div class="finish-notes">
        <span class="hold">medium hold</span>
        <span class="finish">matte finish</span>
      </div>
    </section>
  </main>
</body>
</html>
```